Need a new logo/business card for a cafe

I need a new logo and business card for a café. The café is called "Ladle", and we have a reputation for making a high quality cup of espresso coffee. I would like the business card design to reflect this "high quality". Our baristas craft our customers coffee with care to achieve this result. I would like to see designs that include a warm latte brown color. The card will be single sided to allow the rear to be used as a loyalty card which means the design will need to include space for our business address, phone number, and social page page details. The uploaded logo is already in use on the café front window, and if it can be incorporated or used that would be great, but I am open to completely new designs as well. Thank you.
Updates
Thank you to all for the submissions. There's quite a few I like now, the hardest part will be choosing! I've set up a poll for added feedback from my own contacts and will wait on results from that.
Hello, more great designs coming in, thank you very much. There's quite a few that I really like, so my biggest challenge is going to be choosing one. Thanks again for your time, and I'll get onto the hard task of making that choice. Miriam
Industry/Entity Type
Cafe
Look and feel
Each slider illustrates characteristics of the customer's brand and the style your logo design should communicate.

```html
<!DOCTYPE html>
<html lang="en">
<head>
<meta charset="utf-8">
<title>Ladle – Business Card</title>
<link href="https://fonts.googleapis.com/css2?family=Arvo&display=swap" rel="stylesheet">
<style>
  :root {
    --backdrop: #2b2a29;
    --card-white: #ffffff;
    --latte: #9b8878;
    --mocha: #6f6156;
    --crema: #8e7c6e;
    --espresso: #4a3f38;
    --text-light: #ffffff;
  }
  html, body {
    margin: 0;
    padding: 0;
    width: 1200px;
    height: 686px;
    overflow: hidden;
    background: var(--backdrop);
  }
  .canvas {
    position: relative;
    width: 1200px;
    height: 686px;
  }
  .business-card {
    position: absolute;
    left: 81px;
    top: 23px;
    width: 1038px;
    height: 640px;
    border-radius: 54px;
    overflow: hidden;
    background: var(--card-white);
  }
  .card-bands {
    position: absolute;
    inset: 0;
    width: 100%;
    height: 100%;
    display: block;
  }
  .band-mocha { fill: var(--mocha); }
  .band-crema { fill: var(--crema); }
  .band-espresso { fill: var(--espresso); }
  .band-latte { fill: var(--latte); }
  .brand-name {
    position: absolute;
    left: 0;
    right: 0;
    top: 122px;
    margin: 0;
    text-align: center;
    font-family: "Arvo", serif;
    font-weight: 400;
    font-size: 160px;
    line-height: 1;
    color: var(--latte);
    letter-spacing: 2px;
  }
  .contact-details {
    position: absolute;
    left: 0;
    right: 0;
    top: 478px;
    margin: 0;
    text-align: center;
    font-family: "Arvo", serif;
    font-weight: 400;
    font-size: 37px;
    line-height: 46px;
    color: var(--text-light);
    font-style: normal;
  }
</style>
</head>
<body>
<main class="canvas">
  <section class="business-card">
    <svg class="card-bands" viewBox="0 0 792 488" preserveAspectRatio="none" aria-hidden="true">
      <path class="band-mocha" d="M0 293 Q396 333 792 296 L792 488 L0 488 Z"/>
      <rect class="band-crema" x="0" y="318" width="792" height="15"/>
      <rect class="band-espresso" x="0" y="333" width="792" height="23"/>
      <path class="band-latte" d="M0 356 Q396 311 792 356 L792 488 L0 488 Z"/>
    </svg>
    <h1 class="brand-name">Ladle</h1>
    <address class="contact-details">
      business address<br>
      phone number<br>
      and social page
    </address>
  </section>
</main>
</body>
</html>
```